Business Card design for law firm = Brightvale Australia

We are seeking a new design for our business cards.
We are keeping our logo, which is attached.
We need space for
Name
Title
Address is , which is
Level 7
214 Marlowe Street
Sydney NSW 2047
Phone :
Mobile :
Fax :
Email :
DX :
website www.brightvale-example.com.au

Industry/Entity Type

Law Firm / Banking and Finance

Contact Information for Business Card

We are seeking a new design for our business cards. We are keeping our logo. We need space for Name Title Address is Level 7 214 Marlowe Street Sydney NSW 2047 Phone Mobile Fax Email DX website www.brightvale-example.com.au

Colors
0054AA
0677BA
7BADD7
CADEEF
E8F1F8

Requirements
Must have
• see our website for general feel www.brightvale-example.com.au

```html
<!DOCTYPE html>
<html lang="en">
<head>
<meta charset="utf-8">
<title>Brightvale Australia — Business Card</title>
<link rel="stylesheet" href="https://fonts.googleapis.com/css2?family=Nunito+Sans:wght@400;700;800&display=swap">
<style>
  :root {
    --backdrop: #ababab;
    --card-light: #f4f8fb;
    --card-light-edge: #e8f1f8;
    --card-dark: #0b2240;
    --brand-blue: #0054aa;
    --brand-mid: #0677ba;
    --text-body: #2e3540;
    --watermark-light: rgba(255, 255, 255, 0.92);
    --watermark-dark: rgba(0, 10, 30, 0.35);
    --mark-muted: #3e5b80;
  }
  * { margin: 0; padding: 0; box-sizing: border-box; }
  html, body {
    width: 1200px;
    height: 1000px;
    overflow: hidden;
    background: var(--backdrop);
    font-family: "Nunito Sans", Arial, sans-serif;
  }
  .canvas { position: relative; width: 1200px; height: 1000px; }

  .card {
    position: absolute;
    width: 514px;
    height: 296px;
    overflow: hidden;
  }
  .card--front {
    left: 59px;
    top: 474px;
    background: linear-gradient(135deg, #ffffff 0%, var(--card-light) 50%, var(--card-light-edge) 100%);
  }
  .card--back {
    left: 623px;
    top: 265px;
    background: var(--card-dark);
  }

  .card__watermark {
    position: absolute;
    left: 16px;
    top: -20px;
    font-size: 104px;
    font-weight: 800;
    letter-spacing: -4px;
    line-height: 1;
    white-space: nowrap;
  }
  .card--front .card__watermark { color: var(--watermark-light); }
  .card--back .card__watermark { color: var(--watermark-dark); top: 8px; }

  .contact {
    position: absolute;
    left: 52px;
    top: 124px;
    font-size: 10.5px;
    line-height: 13px;
    color: var(--text-body);
  }
  .contact__name { font-weight: 700; color: var(--brand-blue); }
  .contact__title { color: var(--brand-mid); }
  .contact__group { margin-top: 13px; }

  .brand {
    position: absolute;
    right: 31px;
    bottom: 28px;
    text-align: right;
  }
  .brand__name {
    font-size: 21px;
    font-weight: 400;
    line-height: 1;
  }
  .brand__tagline {
    margin-top: 4px;
    font-size: 9.5px;
    font-weight: 400;
    letter-spacing: 0.4px;
  }
  .card--front .brand__name { color: var(--brand-blue); }
  .card--front .brand__tagline { color: var(--brand-mid); }
  .card--back .brand { right: 30px; bottom: 30px; }
  .card--back .brand__name,
  .card--back .brand__tagline { color: var(--mark-muted); }
</style>
</head>
<body>
<main class="canvas">
  <section class="card card--front" aria-label="Business card front">
    <div class="card__watermark" aria-hidden="true">Brightvale</div>
    <div class="contact">
      <div class="contact__name">Helena Marsh</div>
      <div class="contact__title">Chief Legal Officer</div>
      <div>helena.marsh@brightvale-example.com.au</div>
      <div class="contact__group">
        <div>02 9000 0142</div>
        <div>02 9000 0187</div>
      </div>
      <div class="contact__group">
        <div>Level 7, 214 Marlowe Street</div>
        <div>Sydney NSW 2047, DX 318 Sydney</div>
      </div>
      <div class="contact__group">www.brightvale-example.com.au</div>
    </div>
    <div class="brand">
      <div class="brand__name">Brightvale</div>
      <div class="brand__tagline">strategic legal outsourcing</div>
    </div>
  </section>

  <section class="card card--back" aria-label="Business card back">
    <div class="card__watermark" aria-hidden="true">Brightvale</div>
    <div class="brand">
      <div class="brand__name">Brightvale</div>
      <div class="brand__tagline">strategic legal outsourcing</div>
    </div>
  </section>
</main>
</body>
</html>
```